Mobile Fitness snd Therapy Business Card Design

I need a business card designed for my mobile fitness and therapy business.

Please view the images that I have uploaded. I like the simplicity of the design that I have attached. I adapted it with my information

Target Market(s)

Those seeking personal training, injury rehabilitation or massage therapy.

Industry/Entity Type

Business

Contact Information for Business Card

Derek Fulham - MSc, CAT(C), RMT, CSCS, Pn2
e-mail: derek@vantrelo.com
website: www.vantrelo.com
instagram: @derek_fulham

Font styles to use
Sans Serif

Colors
3176b5
0355a3

Requirements
Must have
• "Contact us to receive a FREE assessment"
• Services offered:
• Personal Training
• Golf Fitness
• Injury Rehab
• Massage Therapy
• Yoga
Nice to have
• Consistent colours with brand
• - Dark Blue: #232837
• - Blue: #5096f0
• Consistent look/feel with the website: www.vantrelo.com

```html
<!DOCTYPE html>
<html lang="en">
<head>
<meta charset="utf-8">
<title>Vantrelo Business Card</title>
<link rel="stylesheet" href="https://fonts.googleapis.com/css2?family=Roboto:wght@400;500;700&family=Roboto+Condensed:wght@500;700&display=swap">
<style>
  :root {
    --page-bg: #e8e6e3;
    --card-white: #f7f7f7;
    --navy: #222838;
    --brand-blue: #2b5ed8;
    --sky-blue: #5096f0;
    --text-grey: #3a3d45;
    --divider: #b9bcc2;
    --white: #ffffff;
  }
  * { margin: 0; padding: 0; box-sizing: border-box; }
  html, body {
    width: 1200px; height: 960px; overflow: hidden;
    background: var(--page-bg);
    font-family: "Roboto", Arial, sans-serif;
  }
  .canvas { position: relative; width: 1200px; height: 960px; }

  .card {
    position: absolute; width: 600px; height: 343px;
    border-radius: 18px; overflow: hidden;
  }

  /* Front */
  .card-front { left: 314px; top: 113px; background: var(--card-white); }
  .brand-name {
    position: absolute; left: 0; right: 0; top: 82px;
    text-align: center;
    font-family: "Roboto", Arial, sans-serif; font-weight: 700;
    font-size: 50px; letter-spacing: 5px; color: var(--navy);
    line-height: 1;
  }
  .brand-tagline {
    position: absolute; left: 0; right: 0; top: 136px;
    text-align: center; font-weight: 700; font-size: 15px;
    letter-spacing: 2.6px; color: var(--navy);
  }
  .holder {
    position: absolute; right: 322px; top: 208px; text-align: right;
    font-family: "Roboto Condensed", Arial, sans-serif; color: var(--brand-blue);
  }
  .holder-name { font-size: 23px; font-weight: 700; line-height: 1.1; }
  .holder-credentials { font-size: 10.5px; font-weight: 700; margin-top: 3px; }
  .divider {
    position: absolute; left: 291px; top: 197px; width: 1px; height: 60px;
    background: var(--divider);
  }
  .contact-list { position: absolute; left: 308px; top: 198px; list-style: none; }
  .contact-item {
    display: flex; align-items: center; gap: 8px;
    height: 19px; font-size: 14px; color: var(--text-grey);
  }
  .contact-icon { width: 13px; height: 13px; flex: none; }
  .card-band { position: absolute; left: 0; bottom: 0; width: 600px; height: 13px; }

  /* Back */
  .card-back { left: 311px; top: 472px; background: var(--navy); }
  .back-brand {
    position: absolute; left: 0; right: 0; top: 118px; text-align: center;
    font-weight: 700; font-size: 44px; letter-spacing: 5px; color: var(--sky-blue);
    line-height: 1;
  }
  .offer {
    position: absolute; left: 58px; top: 259px; width: 483px; height: 32px;
    border-radius: 16px; background: var(--brand-blue);
    font-family: "Roboto Condensed", Arial, sans-serif; font-weight: 700;
    font-size: 20px; color: var(--white);
    display: flex; align-items: center; justify-content: center;
  }
  .services {
    position: absolute; left: 0; right: 0; top: 297px; text-align: center;
    font-size: 14.5px; color: var(--white); list-style: none;
  }
  .services li { display: inline; }
  .services li + li::before { content: "|"; color: var(--sky-blue); margin: 0 5px; }
</style>
</head>
<body>
<main class="canvas">
  <section class="card card-front" aria-label="Card front">
    <div class="brand-name">VANTRELO</div>
    <div class="brand-tagline">NUTRITION - FITNESS - HEALTH</div>

    <div class="holder">
      <div class="holder-name">DEREK FULHAM</div>
      <div class="holder-credentials">MSC, CAT(C), RMT, CSCS, PN2</div>
    </div>
    <div class="divider"></div>

    <ul class="contact-list">
      <li class="contact-item">
        <svg class="contact-icon" viewBox="0 0 13 13"><rect x="0.5" y="2.5" width="12" height="8" rx="1" fill="var(--brand-blue)"/><path d="M1 3.2 6.5 7.2 12 3.2" fill="none" stroke="#fff" stroke-width="1.1"/></svg>
        derek@vantrelo.com
      </li>
      <li class="contact-item">
        <svg class="contact-icon" viewBox="0 0 13 13"><circle cx="6.5" cy="6.5" r="6" fill="var(--brand-blue)"/><ellipse cx="6.5" cy="6.5" rx="2.4" ry="5.6" fill="none" stroke="#fff" stroke-width="0.9"/><path d="M1 6.5h11" stroke="#fff" stroke-width="0.9"/></svg>
        www.vantrelo.com
      </li>
      <li class="contact-item">
        <svg class="contact-icon" viewBox="0 0 13 13"><circle cx="6.5" cy="6.5" r="6" fill="var(--brand-blue)"/></svg>
        @derek_fulham
      </li>
    </ul>

    <svg class="card-band" viewBox="0 0 600 13" preserveAspectRatio="none">
      <rect x="0" y="0" width="600" height="13" fill="var(--navy)"/>
      <polygon points="393,0 600,0 600,13 390,13" fill="var(--white)"/>
      <polygon points="396,0 600,0 600,13 393,13" fill="var(--brand-blue)"/>
    </svg>
  </section>

  <section class="card card-back" aria-label="Card back">
    <div class="back-brand">VANTRELO</div>
    <div class="offer">CONTACT US TO RECEIVE A FREE ASSESSMENT</div>
    <ul class="services">
      <li>Personal Training</li><li>Golf Fitness</li><li>Injury Rehab</li><li>Massage Therapy</li><li>Yoga</li>
    </ul>
  </section>
</main>
</body>
</html>
```